Custom Woodworking and Rock Design

We specialize in original, high quality, wood and rock art. It’s should be self explanatory ask questions if you need. Your team designing a logo. Furniture is custom made to order. Rocks are designed depending on consumer needs. Wood and rock can also be combined for custom work. Painted rocks on vintage wood. Custom chairs and cabinets. Artistic rocks for multiple uses:garden, magnets, custom. All ideas and requests are welcome.

Target Market(s)

All

Contact Information for Business Card

Mara Voss
Talbertstonecraft@mailbrook.net

Font styles to use
Sans Serif

Requirements
Must have
• Clear lettering
Nice to have
• Eye catching
Should not have
• Blurr

```html
<!DOCTYPE html>
<html lang="en">
<head>
<meta charset="utf-8">
<title>Talbert Stonecraft – Business Card</title>
<link rel="stylesheet" href="https://fonts.googleapis.com/css2?family=Open+Sans:wght@400;600;700&display=swap">
<style>
  :root {
    --teal: #1389ad;
    --gold: #c8925a;
    --white: #ffffff;
    --page: #e6e8ec;
    --ink-light: #ffffff;
  }
  * { margin: 0; padding: 0; box-sizing: border-box; }
  html, body { width: 1200px; height: 945px; overflow: hidden; }
  body {
    background: var(--page);
    font-family: "Open Sans", sans-serif;
    position: relative;
  }
  .card {
    position: absolute;
    left: 270px;
    width: 660px;
    height: 378px;
    border-radius: 22px;
    overflow: hidden;
    box-shadow: 0 6px 18px rgba(0,0,0,0.18);
  }
  .card--front { top: 70px; background: var(--teal); }
  .card--back { top: 497px; background: var(--white); }

  .brand {
    display: flex;
    align-items: center;
    gap: 14px;
    color: var(--gold);
    font-weight: 700;
    text-transform: uppercase;
    letter-spacing: 0.5px;
    white-space: nowrap;
  }
  .brand__mark {
    width: 22px; height: 22px;
    flex: none;
    background: var(--gold);
  }
  .card--front .brand {
    position: absolute;
    left: 50%; top: 50%;
    transform: translate(-50%, -50%);
    font-size: 38px;
  }

  .back__band {
    position: absolute; inset: 0;
    width: 100%; height: 100%;
  }
  .back__tab {
    position: absolute;
    left: 0; top: 40px;
    width: 10px; height: 54px;
    background: var(--gold);
    border-radius: 0 6px 6px 0;
  }
  .contact {
    position: absolute;
    left: 38px; top: 40px;
    color: var(--ink-light);
  }
  .contact__name {
    font-size: 26px; font-weight: 700;
    text-transform: uppercase; letter-spacing: 0.5px;
    line-height: 1.1;
  }
  .contact__role {
    font-size: 17px; color: var(--gold);
    margin-bottom: 22px;
  }
  .contact__list { list-style: none; }
  .contact__item {
    display: flex; align-items: center; gap: 12px;
    font-size: 16px; line-height: 1.75;
    white-space: nowrap;
  }
  .contact__icon { width: 18px; height: 18px; flex: none; }
  .card--back .brand {
    position: absolute;
    left: 525px; top: 50%;
    transform: translate(-50%, -50%);
    font-size: 26px;
    line-height: 1.15;
  }
  .card--back .brand__name { display: flex; flex-direction: column; }
</style>
</head>
<body>
  <section class="card card--front" aria-label="Card front">
    <div class="brand">
      <span class="brand__mark"></span>
      <span class="brand__name">Talbert Stonecraft</span>
    </div>
  </section>

  <section class="card card--back" aria-label="Card back">
    <svg class="back__band" viewBox="0 0 660 378" preserveAspectRatio="none" aria-hidden="true">
      <polygon points="0,0 420,0 335,378 0,378" fill="var(--teal)"/>
    </svg>
    <span class="back__tab"></span>
    <div class="contact">
      <p class="contact__name">Mara Voss</p>
      <p class="contact__role">Director</p>
      <ul class="contact__list">
        <li class="contact__item">
          <svg class="contact__icon" viewBox="0 0 20 20" aria-hidden="true"><path d="M5 2h3l1.5 4-2 1.5a11 11 0 0 0 5 5L14 10.5l4 1.5v3a2 2 0 0 1-2 2A14 14 0 0 1 3 4a2 2 0 0 1 2-2z" fill="var(--gold)"/></svg>
          555-014-2873
        </li>
        <li class="contact__item">
          <svg class="contact__icon" viewBox="0 0 20 20" aria-hidden="true"><rect x="2" y="4" width="16" height="12" fill="var(--gold)"/><path d="M2 4l8 7 8-7" stroke="var(--teal)" stroke-width="1.5" fill="none"/></svg>
          Talbertstonecraft@mailbrook.net
        </li>
        <li class="contact__item">
          <svg class="contact__icon" viewBox="0 0 20 20" aria-hidden="true"><rect x="2" y="3" width="16" height="11" rx="1" fill="none" stroke="var(--gold)" stroke-width="2"/><rect x="7" y="15" width="6" height="2" fill="var(--gold)"/></svg>
          www.talbertstonecraft.net
        </li>
      </ul>
    </div>
    <div class="brand">
      <span class="brand__mark"></span>
      <span class="brand__name"><span>Talbert</span><span>Stonecraft</span></span>
    </div>
  </section>
</body>
</html>
```